New Business Card Design for Manufacturing

We are an engineering/manufacturing company that offers Advanced machining/assembly/engineering services, as well as innovative products for the heavy duty engine cooling markets.

We are looking to get a new business card designed that is clean and modern looking, but still fits the wide range of technical/skilled work we do.

- We hope to use this design as the base for other design work in new Presentations, web, and print work.

Industry/Entity Type

Engineering

Contact Information for Business Card

Our preferred color of blue is (RGB) 22/71/159 but can vary slightly from that color. Our content will be our Logo and full company name (Vantrell Forge Works, Inc.), company address, name, job title, phone number with extension, cell number, fax number, website, and email address on the cards.
We'd like the full company name next to the logo, but we are open to other interpretations of that layout.
Preferably, we would like the back side to be clean with just our logo, and the front to contain all of the contact information.

Colors
2f74b4
0355a3
85abd2

Requirements
Must have
• - Logo, company name, needed content - We are open to interpretation beyond that.
• - Standard size business card.
• - Horizontal orientation.
• - Enough space for lengthy names / job titles (for example, a job title could read "Directory of Human Resources" or "V.P. of Governmental Affairs"). We need this to look clean, whether the title be short (CEO) or long (as described above).

```html
<!DOCTYPE html>
<html lang="en">
<head>
<meta charset="utf-8">
<title>Vantrell Forge Works – Business Card</title>
<link rel="stylesheet" href="https://fonts.googleapis.com/css2?family=Arimo:wght@400;700&display=swap">
<style>
  :root {
    --brand-blue: #16479f;
    --band-blue: #0f55a6;
    --band-blue-deep: #16479f;
    --steel-grey: #7d8287;
    --text-dark: #2b2b2b;
    --card-white: #ffffff;
    --card-tint: #f3f3f3;
    --backdrop: #e4e6e9;
  }
  * { margin: 0; padding: 0; box-sizing: border-box; }
  html, body {
    width: 1200px; height: 900px; overflow: hidden;
    background: var(--backdrop);
    font-family: "Arimo", Arial, sans-serif;
  }
  .stage { position: relative; width: 1200px; height: 900px; }
  .card {
    position: absolute; width: 540px; height: 309px;
    box-shadow: 0 6px 18px rgba(0,0,0,.18);
    overflow: hidden;
  }
  /* Back side */
  .card-back { left: 40px; top: 296px; background: var(--card-white); }
  .back-lockup {
    position: absolute; left: 0; right: 0; top: 92px;
    display: flex; justify-content: center; align-items: center; gap: 14px;
  }
  .brand-mark { width: 26px; height: 26px; background: var(--brand-blue); flex: none; }
  .brand-name {
    color: var(--brand-blue); font-weight: 700; font-size: 30px;
    letter-spacing: .5px; line-height: 1;
  }
  .company-full {
    color: var(--brand-blue); font-weight: 700; font-size: 13px;
    line-height: 1.05; text-transform: uppercase; letter-spacing: .5px;
  }
  .tagline {
    color: var(--steel-grey); font-weight: 700; font-size: 12px;
    text-transform: uppercase; letter-spacing: .6px;
  }
  .back-tagline { position: absolute; left: 0; right: 0; top: 136px; text-align: center; }
  .back-web {
    position: absolute; left: 0; right: 0; top: 228px; text-align: center;
    color: var(--brand-blue); font-weight: 700; font-size: 13px; letter-spacing: 2px;
  }
  /* Front side */
  .card-front { left: 620px; top: 296px; background: var(--card-tint); }
  .accent-band {
    position: absolute; left: 0; right: 0; bottom: 0; height: 44px;
    background: linear-gradient(90deg, var(--band-blue-deep), var(--band-blue));
  }
  .person { position: absolute; left: 40px; top: 52px; }
  .person-name {
    color: var(--brand-blue); font-size: 21px; font-weight: 400;
    letter-spacing: .5px; text-transform: uppercase; line-height: 1.1;
  }
  .person-title { color: var(--text-dark); font-size: 14px; margin-top: 3px; }
  .front-lockup { position: absolute; right: 30px; top: 44px; }
  .front-lockup .brand-row { display: flex; align-items: center; gap: 10px; }
  .front-lockup .brand-name { font-size: 32px; }
  .front-lockup .tagline { margin-top: 6px; font-size: 13px; }
  .contact {
    position: absolute; left: 40px; top: 136px; list-style: none;
    font-size: 14px; color: var(--text-dark);
  }
  .contact li { display: flex; align-items: center; gap: 8px; height: 19px; }
  .contact svg { width: 12px; height: 12px; fill: var(--brand-blue); flex: none; }
  .contact .address { margin-top: 2px; }
  .front-web {
    position: absolute; right: 24px; bottom: 15px;
    color: var(--card-white); font-size: 12px;
  }
</style>
</head>
<body>
<main class="stage">

  <section class="card card-back" aria-label="Business card back">
    <div class="back-lockup">
      <span class="brand-mark"></span>
      <span class="brand-name">Vantrell</span>
      <span class="company-full">Vantrell<br>Forge<br>Works, Inc.</span>
    </div>
    <p class="tagline back-tagline">Built for the Long Haul</p>
    <p class="back-web">WWW.WEBSITENAME.COM</p>
  </section>

  <section class="card card-front" aria-label="Business card front">
    <div class="accent-band" role="img" aria-label="Decorative blue and grey wave band along the lower edge"></div>

    <div class="person">
      <h1 class="person-name">Jonathan Smith</h1>
      <p class="person-title">Managing Director</p>
    </div>

    <div class="front-lockup">
      <div class="brand-row">
        <span class="brand-mark"></span>
        <span class="brand-name">Vantrell</span>
      </div>
      <p class="tagline">Built for the Long Haul</p>
    </div>

    <ul class="contact">
      <li><svg viewBox="0 0 12 12" aria-hidden="true"><path d="M1,4 C1,2 3,1 6,1 C9,1 11,2 11,4 L8.5,4.5 L8,3 L4,3 L3.5,4.5 Z M3,6 L9,6 L10,11 L2,11 Z"/></svg>(044)123456789</li>
      <li><svg viewBox="0 0 12 12" aria-hidden="true"><path d="M3,0 H9 V12 H3 Z M4,1.5 V9 H8 V1.5 Z"/></svg>(044)123456789</li>
      <li><svg viewBox="0 0 12 12" aria-hidden="true"><path d="M3,0 H9 V3 H11 V11 H1 V3 H3 Z M4,1 V3 H8 V1 Z M3,5 V7 H9 V5 Z"/></svg>(044)123456789</li>
      <li><svg viewBox="0 0 12 12" aria-hidden="true"><path d="M0,2 H12 V10 H0 Z M1,3 L6,7 L11,3 Z"/></svg>info@youremail.com</li>
      <li class="address">1234, Address GoesHere,</li>
      <li class="address">Country name, 12345</li>
    </ul>

    <p class="front-web">www.websitename.com</p>
  </section>

</main>
</body>
</html>
```